High-end law practice specializing in closely held business succession planning and complex estates

Solo practitioner whose practice specializes in high-net worth, complex estate planning needs muliple versions of letterhead black and white, please. Letterhead should incorporate slogan, "Guarding What Your Family Has Built," for one and "Complex Estate Planning"; third with no slogan. All for The Law Office of Marcy Lynn Pettibone, PC, 418 Cedar Hollow Ln., Alder Falls, Virginia 23648, Tel. 757-555-0142 Fax tbd email: marcy@mlplawgroup.example; Marcy Lynn Pettibone, Esq., principal, licensed in VA, NY, DC
Updates

Project Deadline Extended
Reason: My internet service went down and I can only view designs on my smart phone -- it's just too hard to review. So sorry! Working with my ISP now. Please be patient!

Target Market(s)

High net worth clients with complex estate planning needs, family businesses, family farmers, family foresters -- people with unique estate/succession planning needs who need a specialist who understands them.

Industry/Entity Type

Business

Font styles to use
Script

Requirements
Must have
• A high-end look and feel, connoting trustworthiness, special knowledge, and expertise.

```html
<!DOCTYPE html>
<html lang="en">
<head>
<meta charset="utf-8">
<title>Letterhead – The Law Office of Marcy Lynn Pettibone, PC</title>
<link href="https://fonts.googleapis.com/css2?family=EB+Garamond:wght@400;600;700&family=Open+Sans:wght@400;600&family=Dancing+Script:wght@500&display=swap" rel="stylesheet">
<style>
  :root {
    --backdrop: #e9e9e9;
    --paper: #ffffff;
    --ink: #1a1a1a;
    --body-ink: #4a4a4a;
    --rule: #2a2a2a;
    --band: #0c0c0c;
    --band-text: #ffffff;
    --signature: #1f2f8f;
  }
  * { box-sizing: border-box; margin: 0; padding: 0; }
  html, body {
    width: 1200px; height: 795px; overflow: hidden;
    background: var(--backdrop);
  }
  .letterhead {
    position: absolute; left: 330px; top: 16px;
    width: 540px; height: 763px;
    background: var(--paper);
    box-shadow: 0 2px 10px rgba(0,0,0,.12);
    color: var(--ink);
    font-family: "Open Sans", Arial, sans-serif;
  }
  .masthead {
    position: absolute; left: 44px; top: 44px; right: 44px;
    border-bottom: 1px solid var(--rule);
    padding-bottom: 4px;
  }
  .firm-name {
    font-family: "EB Garamond", "Times New Roman", serif;
    font-weight: 700; font-size: 19px; line-height: 1.05;
    letter-spacing: .02em; text-transform: uppercase;
  }
  .slogan {
    position: absolute; right: 44px; top: 100px;
    font-family: "EB Garamond", "Times New Roman", serif;
    font-size: 10.5px;
  }
  .letter {
    position: absolute; left: 56px; top: 140px; width: 420px;
    font-size: 8.6px; line-height: 1.45; color: var(--body-ink);
  }
  .date { margin-bottom: 10px; }
  .recipient { margin-bottom: 12px; font-style: normal; }
  .salutation { font-weight: 600; color: var(--ink); margin-bottom: 8px; }
  .letter p.body { margin-bottom: 12px; text-align: justify; }
  .closing { margin-top: 18px; }
  .signature {
    font-family: "Dancing Script", cursive;
    color: var(--signature); font-size: 24px; line-height: 1.1;
    margin: 2px 0 2px 6px;
  }
  .footer-contact {
    position: absolute; right: 44px; bottom: 110px;
    text-align: right;
    font-family: "EB Garamond", "Times New Roman", serif;
    font-size: 10px; line-height: 1.45;
  }
  .footer-contact .footer-firm { font-weight: 700; }
  .contact-line { display: inline-flex; align-items: center; gap: 3px; margin-left: 4px; }
  .contact-line svg { width: 8px; height: 8px; fill: var(--ink); }
  .practice-band {
    position: absolute; left: 0; bottom: 28px;
    width: 250px; height: 30px;
    background: var(--band); color: var(--band-text);
    border-radius: 0 15px 15px 0;
    display: flex; align-items: center; justify-content: center;
    font-family: "EB Garamond", "Times New Roman", serif;
    font-size: 15px; letter-spacing: .02em;
  }
</style>
</head>
<body>
  <main class="letterhead">
    <header class="masthead">
      <h1 class="firm-name">The Law Office<br>of Marcy Lynn Pettibone</h1>
    </header>
    <p class="slogan">Guarding What Your Family Has Built</p>

    <section class="letter">
      <p class="date">January 12, 2014</p>
      <address class="recipient">
        Mr. John Doe<br>President<br>AA Corporation<br>111 Street Name, Suite#<br>City, State, 12345
      </address>
      <p class="salutation">Dear Mr. John,</p>
      <p class="body">Lorem Ipsum is simply dummy text of the printing and typesetting industry. Lorem Ipsum has been the industry's standard dummy text ever since the 1500s, when an unknown printer took a galley of type and scrambled it to make a type specimen book. It has survived not only five centuries, but also the leap into electronic typesetting, remaining essentially unchanged.</p>
      <p class="body">The standard chunk of Lorem Ipsum used since the 1500s is reproduced below for those interested. Sections 1.10.32 and 1.10.33 from "de Finibus Bonorum et Malorum" by Cicero are also reproduced in their exact original form, accompanied by English versions from the 1914 translation by H. Rackham.</p>
      <p class="body">Lorem Ipsum is simply dummy text of the printing and typesetting industry. Lorem Ipsum has been the industry's standard dummy text ever since the 1500s, when an unknown printer took a galley of type and scrambled it to make a type specimen book. It has survived not only five centuries, but also the leap into electronic typesetting, remaining essentially unchanged. It was popularised in the</p>
      <div class="closing">
        <p>Sincerely Your,</p>
        <p class="signature">your name</p>
        <p>Name Last Name<br>Company Name</p>
      </div>
    </section>

    <footer class="footer-contact">
      <p class="footer-firm">The Law Office of Marcy Lynn Pettibone</p>
      <p>PC, 418 Cedar Hollow Ln., Alder Falls, Virginia 23648,</p>
      <p>
        <span class="contact-line"><svg viewBox="0 0 10 10"><path d="M2 1h2l1 2.5-1.2 1a6 6 0 0 0 2.7 2.7l1-1.2L10 7v2c0 .6-.4 1-1 1A9 9 0 0 1 0 1c0-.6.4-1 1-1z"/></svg>757-555-0142</span>
        <span class="contact-line"><svg viewBox="0 0 10 10"><path d="M2 0h5v3H2zM0 4h10v5H0zm2 1v1h2V5z"/></svg>757-555-0178</span>
        <span class="contact-line"><svg viewBox="0 0 10 10"><path d="M0 2h10v6H0zm1 1v.3l4 2.7 4-2.7V3z"/></svg>marcy@mlplawgroup.example</span>
      </p>
    </footer>

    <div class="practice-band">Complex Estate Planning</div>
  </main>
</body>
</html>
```